Business card for my new company (Accounting firm)

I need a business card for my new business Brightwell Advisory and Ledger SA. Our services are accounting, tax, audit and financial management. Our customers are small companies, start-ups and new companies. The final design has to show financial security, trust and growth. Please find our logo attached to the business card. Text for the business card: Brightwell Advisory and Ledger SA Tomas Varenholt Director and Founder Certified Accountant Tel. 022 418 57 34 tv@clairevalconseil.ch www.clairevalconseil.ch Rue des Vergières 27 1201 Geneva
Target Market(s)
Our customers are small companies, start-ups and new companies.
Industry/Entity Type
Finance And Accounting
Contact Information for Business Card
Claireval Conseil et Comptes SA
Tomas Varenholt
Directeur et Fondateur
Expert-comptable diplômé
Tél. 022 418 57 34
tv@clairevalconseil.ch
www.clairevalconseil.ch
Rue des Vergières 27
1201 Genève

```html
<!DOCTYPE html>
<html lang="fr">
<head>
<meta charset="utf-8">
<title>Claireval Conseil et Comptes SA – Carte de visite</title>
<link rel="stylesheet" href="https://fonts.googleapis.com/css2?family=Roboto:wght@400;500;700&display=swap">
<style>
  :root {
    --bg: #e6e7e9;
    --paper: #f4f4f4;
    --ink: #333538;
    --ink-soft: #4a4c50;
    --blue-light: #2ba3d6;
    --blue-mid: #1f7fb8;
    --blue-deep: #175a8a;
    --title-blue: #1d5c96;
    --white: #ffffff;
  }
  * { box-sizing: border-box; margin: 0; padding: 0; }
  html, body { width: 1200px; height: 726px; overflow: hidden; }
  body {
    background: var(--bg);
    font-family: "Roboto", Arial, sans-serif;
    position: relative;
  }
  .card {
    position: absolute;
    top: 204px;
    width: 540px;
    height: 318px;
    border-radius: 4px;
    box-shadow: 0 6px 18px rgba(0,0,0,0.12);
    overflow: hidden;
  }
  /* Back side */
  .card-back {
    left: 40px;
    background: linear-gradient(160deg, var(--blue-light) 0%, var(--blue-mid) 60%, var(--blue-deep) 100%);
    color: var(--white);
    display: flex;
    flex-direction: column;
    align-items: center;
    justify-content: center;
  }
  .card-back .company {
    font-weight: 500;
    font-size: 30px;
    letter-spacing: 1px;
    margin-top: -20px;
  }
  .card-back .web {
    position: absolute;
    bottom: 44px;
    font-size: 15px;
    font-weight: 500;
    letter-spacing: 0.5px;
  }
  /* Front side */
  .card-front {
    left: 620px;
    background: var(--paper);
    color: var(--ink);
  }
  .card-front .company {
    position: absolute;
    left: 34px;
    top: 44px;
    font-weight: 500;
    font-size: 25px;
    color: var(--ink);
    letter-spacing: 0.3px;
  }
  .side-band {
    position: absolute;
    right: 0;
    top: 0;
    width: 36px;
    height: 100%;
    display: flex;
    flex-direction: column;
  }
  .side-band span { flex: 1; }
  .side-band .b1 { background: var(--blue-light); }
  .side-band .b2 { background: var(--blue-mid); }
  .side-band .b3 { background: var(--blue-deep); }
  .person {
    position: absolute;
    left: 34px;
    top: 116px;
  }
  .person .name {
    font-weight: 700;
    font-size: 20px;
    color: var(--title-blue);
  }
  .person .role {
    font-size: 13px;
    color: var(--ink-soft);
    line-height: 1.35;
    margin-top: 3px;
  }
  .contacts {
    position: absolute;
    left: 34px;
    top: 196px;
    list-style: none;
    font-size: 14.5px;
    color: var(--ink);
  }
  .contacts li {
    display: flex;
    align-items: center;
    gap: 10px;
    height: 22px;
  }
  .contacts svg { width: 14px; height: 14px; fill: var(--title-blue); flex: none; }
  .address {
    position: absolute;
    left: 34px;
    top: 270px;
    font-size: 14.5px;
    color: var(--ink);
  }
</style>
</head>
<body>
  <section class="card card-back" aria-label="Verso de la carte">
    <p class="company">Claireval Conseil et Comptes</p>
    <p class="web">www.clairevalconseil.ch</p>
  </section>

  <section class="card card-front" aria-label="Recto de la carte">
    <p class="company">Claireval Conseil et Comptes</p>
    <div class="side-band" aria-hidden="true"><span class="b1"></span><span class="b2"></span><span class="b3"></span></div>
    <div class="person">
      <p class="name">Tomas Varenholt</p>
      <p class="role">Directeur et Fondateur<br>Expert-comptable diplômé</p>
    </div>
    <ul class="contacts">
      <li>
        <svg viewBox="0 0 16 16" aria-hidden="true"><path d="M2 5c0-2 2-3 6-3s6 1 6 3v1h-3V5H5v1H2zM4 7h8l2 7H2z"/></svg>
        022 418 57 34
      </li>
      <li>
        <svg viewBox="0 0 16 16" aria-hidden="true"><path d="M1 3h14v10H1zM2 4.2v.6l6 4 6-4v-.6z"/></svg>
        tv@clairevalconseil.ch
      </li>
      <li>
        <svg viewBox="0 0 16 16" aria-hidden="true"><path d="M8 1a7 7 0 1 0 0 14A7 7 0 0 0 8 1zm0 1.3c.9 0 1.8 1.9 2 4.7H6c.2-2.8 1.1-4.7 2-4.7zM2.4 7a5.7 5.7 0 0 1 2.8-4.2C4.9 4 4.7 5.4 4.7 7zm0 2h2.3c0 1.6.2 3 .5 4.2A5.7 5.7 0 0 1 2.4 9zM8 13.7c-.9 0-1.8-1.9-2-4.7h4c-.2 2.8-1.1 4.7-2 4.7zM10.8 13.2c.3-1.2.5-2.6.5-4.2h2.3a5.7 5.7 0 0 1-2.8 4.2zM11.3 7c0-1.6-.2-3-.5-4.2A5.7 5.7 0 0 1 13.6 7z"/></svg>
        www.clairevalconseil.ch
      </li>
    </ul>
    <p class="address">Rue des Vergières 27 1201 Genève</p>
  </section>
</body>
</html>
```